A website for Kovadrel Limited

We need a new and modern website for our company. We are engineering consultants and contractors (EPC) in the oil and gas industry and building services industry.
What we do:
Engineering, procurement, construction
Automation (safety and process)
Non-destructive testing
Training
We have an existing website and the content can be referred from there since we are remaking the website
For more information visit Kovadrel Limited Kenya

```html
<!DOCTYPE html>
<html lang="en">
<head>
<meta charset="utf-8">
<title>Kovadrel Limited</title>
<link href="https://fonts.googleapis.com/css2?family=Poppins:wght@400;500;600;700;800&display=swap" rel="stylesheet">
<style>
:root{
  --orange:#e8894a;
  --orange-dark:#d9733a;
  --ink:#111111;
  --text:#2a2a2a;
  --pale:#fbf0ee;
  --white:#ffffff;
  --grey:#e9e9ea;
}
*{margin:0;padding:0;box-sizing:border-box}
html,body{width:1200px;height:3496px;overflow:hidden}
body{font-family:'Poppins',sans-serif;color:var(--ink);background:var(--white);position:relative}
.abs{position:absolute}
a{color:inherit;text-decoration:none}
/* header */
.topbar{position:absolute;left:665px;top:0;width:535px;height:65px;background:var(--orange);clip-path:polygon(45px 0,100% 0,100% 100%,0 100%)}
.toplinks{position:absolute;left:730px;top:22px;display:flex;gap:22px;color:var(--white);font-size:15px;font-weight:500}
.brand{position:absolute;left:110px;top:19px;display:flex;align-items:center;gap:4px}
.brand-mark{width:110px;height:118px;border:3px solid var(--orange-dark);border-radius:50%}
.brand-name{font-size:30px;line-height:40px;color:#8a6a62;letter-spacing:.5px}
.nav{position:absolute;left:482px;top:101px;display:flex;gap:20px;font-size:15px;font-weight:500}
/* hero */
.hero{position:absolute;left:0;top:152px;width:1200px;height:545px;background:linear-gradient(110deg,#3d3a36 0%,#7a6a4e 35%,#c79a3c 60%,#5c4b34 100%)}
.hero h1{position:absolute;left:110px;top:114px;font-size:57px;line-height:58px;font-weight:800;color:var(--white)}
.hero p{position:absolute;left:110px;top:235px;width:470px;font-size:15.5px;line-height:20.5px;color:var(--white)}
.btn{position:absolute;background:var(--orange);color:var(--white);font-size:16px;display:flex;align-items:center;justify-content:center}
.h2{position:absolute;left:0;width:1200px;text-align:center;font-size:37px;font-weight:800}
/* values */
.value{position:absolute;width:200px;text-align:center}
.value .dot{width:138px;height:138px;border-radius:50%;background:var(--orange);margin:0 auto;display:flex;align-items:center;justify-content:center}
.value span{display:block;margin-top:24px;font-size:24px;font-weight:600}
/* about */
.about{position:absolute;left:0;top:1067px;width:1200px;height:468px;background:var(--pale)}
.about-img{position:absolute;left:0;top:0;width:640px;height:468px;background:linear-gradient(90deg,#6e6f73 0%,#a6a9ad 55%,rgba(251,240,238,0) 100%)}
.about h2{position:absolute;left:599px;top:60px;font-size:37px;font-weight:800}
.about p{position:absolute;left:599px;top:118px;width:490px;font-size:15.5px;line-height:21.5px;color:var(--text)}
/* services */
.services{position:absolute;left:0;top:1535px;width:1200px;height:600px;background:linear-gradient(180deg,#e8894a,#e4813f)}
.card{position:absolute;width:282px;background:var(--white);text-align:center}
.card .ph{height:178px}
.card h3{font-size:25px;font-weight:600;margin-top:12px}
.card p{font-size:15.5px;line-height:21.5px;color:var(--text);padding:0 18px;margin-top:4px}
.arrow{position:absolute;width:20px;height:20px}
/* clients */
.client{position:absolute;display:flex;align-items:center;justify-content:center;gap:10px;font-size:22px;font-weight:600;color:#333}
.client i{width:22px;height:22px;border-radius:50%;background:var(--orange);display:block}
/* testimonials */
.testi-bg{position:absolute;left:0;top:2511px;width:1200px;height:640px;background:linear-gradient(180deg,#ececee,#dedfe1)}
.tcard{position:absolute;top:2672px;width:282px;height:320px;background:var(--white);padding:14px 24px}
.tcard .row{display:flex;justify-content:space-between;font-size:15.5px;color:#666}
.tcard .stars{color:#f0a030;letter-spacing:1px}
.tcard h4{font-size:18px;line-height:21px;font-weight:600;margin-top:12px}
.tcard p{font-size:15.5px;line-height:21.5px;color:var(--text);margin-top:12px}
.who{display:flex;align-items:center;gap:10px;margin-top:12px;font-size:15px;line-height:24px}
.who .av{width:70px;height:70px;border-radius:50%;background:linear-gradient(180deg,#b9b9bb,#56575b)}
/* footer */
.footer{position:absolute;left:0;top:3122px;width:1200px;height:374px;background:var(--orange);color:var(--white)}
.footer .col{position:absolute;top:81px;font-size:15.5px;line-height:22.4px}
.footer b{font-weight:500}
.flinks{position:absolute;left:0;top:307px;width:1200px;text-align:center;font-size:16px}
.fline{position:absolute;left:110px;top:340px;width:977px;height:1px;background:var(--white)}
.copy{position:absolute;left:0;top:349px;width:1200px;text-align:center;font-size:16px}
.social{position:absolute;left:110px;top:248px;display:flex;gap:10px}
.social i{width:20px;height:20px;border:1.5px solid var(--white);border-radius:50%;display:block}
</style>
</head>
<body>

<header>
  <div class="topbar"></div>
  <nav class="toplinks"><a>WHERE WE OPERATE</a><a>OUR PARTNERS</a><a>SHOP</a></nav>
  <div class="brand">
    <div class="brand-mark"></div>
    <div class="brand-name">KOVADREL<br>LIMITED</div>
  </div>
  <nav class="nav"><a>HOME</a><a>ABOUT US</a><a>SERVICES</a><a>PRODUCTS</a><a>OUR PROJECTS</a><a>OUR CLIENTS</a></nav>
</header>

<section class="hero" role="img" aria-label="Gas pipelines at an industrial port with a tanker ship at sunset">
  <h1>WELCOME TO<br>KOVADREL LIMITED</h1>
  <p>Kovadrel undertakes Design, Supply, Installation and Commissioning of LPG and Petroleum systems including LPG Reticulated Systems (piped gas). We also do LPG tank revalidation and recertification</p>
  <a class="btn" style="left:110px;top:339px;width:150px;height:55px">READ MORE</a>
</section>
<svg class="abs" style="left:0;top:600px" width="1200" height="110" viewBox="0 0 1200 110">
  <path d="M0 95 C300 50 600 40 900 55 C1050 62 1150 80 1200 90 L1200 110 L0 110Z" fill="var(--white)"/>
  <path d="M0 95 C300 50 600 40 900 55 C1050 62 1150 80 1200 90" fill="none" stroke="var(--orange)" stroke-width="10"/>
</svg>

<h2 class="h2" style="top:708px">OUR VALUES</h2>
<div class="value" style="left:81px;top:798px"><div class="dot"><svg width="60" height="60" viewBox="0 0 60 60"><circle cx="30" cy="26" r="18" fill="none" stroke="#fff" stroke-width="4"/><path d="M30 16l3 7h7l-5.5 4.5 2 7-6.5-4-6.5 4 2-7L20 23h7z" fill="#fff"/></svg></div><span>Professionalism</span></div>
<div class="value" style="left:290px;top:798px"><div class="dot"><svg width="60" height="60" viewBox="0 0 60 60"><circle cx="30" cy="30" r="9" fill="none" stroke="#fff" stroke-width="5"/><circle cx="30" cy="30" r="20" fill="none" stroke="#fff" stroke-width="3" stroke-dasharray="14 6"/></svg></div><span>Integrity</span></div>
<div class="value" style="left:497px;top:798px"><div class="dot"><svg width="60" height="60" viewBox="0 0 60 60"><circle cx="30" cy="30" r="22" fill="none" stroke="#fff" stroke-width="4"/><circle cx="30" cy="24" r="6" fill="#fff"/><path d="M19 42c2-8 20-8 22 0z" fill="#fff"/></svg></div><span>Customer focus</span></div>
<div class="value" style="left:702px;top:798px"><div class="dot"><svg width="70" height="50" viewBox="0 0 70 50"><path d="M5 18l15-8 15 6 15-6 15 8-10 18-20 8-20-8z" fill="#fff"/></svg></div><span>Respect</span></div>
<div class="value" style="left:910px;top:798px"><div class="dot"><svg width="50" height="64" viewBox="0 0 50 64"><rect x="4" y="6" width="42" height="54" rx="4" fill="#fff"/><path d="M12 22h26M12 34h26M12 46h26" stroke="var(--orange)" stroke-width="4"/></svg></div><span>Accountability</span></div>

<section class="about">
  <div class="about-img" role="img" aria-label="High-rise buildings under construction with tower cranes"></div>
  <h2>ABOUT US</h2>
  <p>Kovadrel undertakes Design, Supply, Installation and Commissioning of LPG and Petroleum systems including LPG Reticulated Systems (piped gas). We also do LPG tank revalidation and recertification.<br>Our clients include: Oil companies (both multinationals and local), government agencies, manufacturing companies, agricultural institutions, and the building services industry. Kovadrel was incorporated in 2010 with the huge potential of the LPG and Petroleum market in Eastern and Central Africa in mind.</p>
  <a class="btn" style="left:599px;top:349px;width:149px;height:55px">READ MORE</a>
</section>

<section class="services">
  <h2 class="h2" style="top:60px;color:var(--white)">WHAT WE DO</h2>
  <svg class="arrow" style="left:62px;top:297px" viewBox="0 0 20 20"><path d="M13 3L6 10l7 7" fill="none" stroke="#fff" stroke-width="2.5"/></svg>
  <svg class="arrow" style="left:1114px;top:297px" viewBox="0 0 20 20"><path d="M7 3l7 7-7 7" fill="none" stroke="#fff" stroke-width="2.5"/></svg>
  <div class="card" style="left:110px;top:156px;height:304px"><div class="ph" role="img" aria-label="Engineers reviewing plans on a construction site" style="background:linear-gradient(180deg,#c9b59a,#8d7a66)"></div><h3>Engineering</h3><p>Lorem Ipsum is simply dummy text. Lorem Ipsum is simply dummy text.</p></div>
  <div class="card" style="left:457px;top:156px;height:304px"><div class="ph" role="img" aria-label="Steel pipework at a processing plant" style="background:linear-gradient(180deg,#4d7fa8,#b8bec4)"></div><h3>Procurement</h3><p>Lorem Ipsum is simply dummy text. Lorem Ipsum is simply dummy text.</p></div>
  <div class="card" style="left:805px;top:156px;height:302px"><div class="ph" role="img" aria-label="Team of workers in hard hats and safety vests" style="background:linear-gradient(180deg,#2f3a4a,#6c7a5a)"></div><h3>Training</h3><p>Lorem Ipsum is simply dummy text. Lorem Ipsum is simply dummy text.</p></div>
</section>
<svg class="abs" style="left:0;top:2055px" width="1200" height="90" viewBox="0 0 1200 90">
  <path d="M0 70 C250 20 600 10 900 25 C1050 33 1150 50 1200 55 L1200 90 L0 90Z" fill="var(--white)"/>
  <path d="M0 70 C250 20 600 10 900 25 C1050 33 1150 50 1200 55" fill="none" stroke="var(--ink)" stroke-width="8"/>
</svg>

<h2 class="h2" style="top:2152px">OUR CLIENTS</h2>
<div class="client" style="left:115px;top:2286px;width:186px;height:112px"><i></i>Greenvale</div>
<div class="client" style="left:410px;top:2276px;width:170px;height:136px"><i></i>Quadrix</div>
<div class="client" style="left:648px;top:2266px;width:174px;height:152px;background:#f3f3f3"><i></i>Digital Brio</div>
<div class="client" style="left:920px;top:2276px;width:160px;height:136px"><i></i>Unityhub</div>

<div class="testi-bg" role="img" aria-label="Faded industrial refinery backdrop"></div>
<h2 class="h2" style="top:2572px">TESTIMONIALS</h2>
<svg class="arrow abs" style="left:52px;top:2816px" viewBox="0 0 20 20"><path d="M13 3L6 10l7 7" fill="none" stroke="#333" stroke-width="2.5"/></svg>
<svg class="arrow abs" style="left:1115px;top:2816px" viewBox="0 0 20 20"><path d="M7 3l7 7-7 7" fill="none" stroke="#333" stroke-width="2.5"/></svg>
<div class="tcard" style="left:110px"><div class="row"><span class="stars">★★★★★</span><span>2 days ago</span></div><h4>Lorem Ipsum is simply dummy text of printing</h4><p>Lorem Ipsum is simply dummy text. Lorem Ipsum is simply dummy text. Lorem Ipsum is simply dummy text. Lorem Ipsum is simply dummy text.</p><div class="who"><div class="av" role="img" aria-label="Portrait photo of client"></div><div>DANE ORUKO<br>NEWYORK</div></div></div>
<div class="tcard" style="left:457px"><div class="row"><span class="stars">★★★★★</span><span>2 days ago</span></div><h4>Lorem Ipsum is simply dummy text of printing</h4><p>Lorem Ipsum is simply dummy text. Lorem Ipsum is simply dummy text. Lorem Ipsum is simply dummy text. Lorem Ipsum is simply dummy text.</p><div class="who"><div class="av" role="img" aria-label="Portrait photo of client"></div><div>TOMAS<br>NEWYORK</div></div></div>
<div class="tcard" style="left:805px"><div class="row"><span class="stars">★★★★★</span><span>2 days ago</span></div><h4>Lorem Ipsum is simply dummy text of printing</h4><p>Lorem Ipsum is simply dummy text. Lorem Ipsum is simply dummy text. Lorem Ipsum is simply dummy text. Lorem Ipsum is simply dummy text.</p><div class="who"><div class="av" role="img" aria-label="Portrait photo of client"></div><div>LEVIN<br>NEWYORK</div></div></div>

<footer class="footer">
  <svg class="abs" style="left:0;top:-40px" width="1200" height="50" viewBox="0 0 1200 50">
    <path d="M0 42 C300 20 600 -5 900 8 C1050 15 1150 25 1200 30 L1200 50 L0 50Z" fill="var(--orange)"/>
    <path d="M450 18 C600 -2 800 0 1000 14" fill="none" stroke="var(--ink)" stroke-width="7"/>
  </svg>
  <div class="brand" style="left:110px;top:25px;gap:2px"><div style="width:68px;height:72px;border:2.5px solid #fff;border-radius:50%"></div><div style="font-size:19px;line-height:25px">KOVADREL<br>LIMITED</div></div>
  <div class="col" style="left:110px;top:130px">Engineering, procurement,<br>construction Automation<br>(safety and process)<br>Non-destructive testing<br>Training.</div>
  <div class="social"><i></i><i></i><i></i></div>
  <div class="abs" style="left:379px;top:36px;font-size:22px;font-weight:700">CONTACT</div>
  <div class="col" style="left:379px"><b>Shop:</b><br>Halden House,<br>Mtoni Link road<br>Industrial Area<br>P.O. Box 40312-00100<br>Nairobi<br>✆ +254 700 555 014<br>✆ +254 711 555 027<br>✉ shop@kovadrel.example</div>
  <div class="col" style="left:634px;top:59px"><b>Head Office:</b><br>Tervel Court,<br>Next to Arbor Mall,<br>Lanet, Suite 14,<br>Riverbend Road<br>P.O. Box 40312-00100<br>Nairobi<br>✆ +254 700 555 014<br>✆ +254 711 555 027<br>✉ info@kovadrel.example</div>
  <div class="col" style="left:920px;top:59px"><b>Kovadrel Rwanda</b><br>Plot number 2207, Nyaruva,<br>Kanombe, Kigali.<br>✆ +250 788 555 031,<br>✆ +254 711 555 027<br>✉ rw@kovadrel.example</div>
  <div class="flinks">About Us &nbsp;.&nbsp; Services &nbsp;.&nbsp; Products &nbsp;.&nbsp; Our Projects &nbsp;.&nbsp; Our clients &nbsp;.&nbsp; Where We Operate &nbsp;.&nbsp; Our Partners</div>
  <div class="fline"></div>
  <div class="copy">©2023kovadrellimited | all rights reserved</div>
</footer>

</body>
</html>
```